74tlq.com - International Brand Needs A Fresh Look

New Company needing an fresh clean look. 74tlqs.com.au

Product: SSLs

Brands: Corvalux, PlinWard, Brimlo, MellowTLS

Encourage all designers that can deliver a clean and fresh design with a touch of imagination.

We don't want this to be your typical boring ssl reseller site, we want the whole process to be fast and transparent. We welcome your design ideas.

Unrelated site designs we like:
www.grendavia.com, www.flomp.com

Backend - Quillora Run

Pages to design:

Home Page - see examples above. looking for fresh ideas!!

Product Page - try and avoid grids or boring/usual ways to display ssl information and product info. looking for fresh ideas!!

Contact us page

Checkout - using quillora run, so not sure how much we can customise on this page

we had thought about an idea using an input box on the home page - that looks like a browser bar where they enter the url they are purchasing for - different way to display this and get them to interact with the site. when they click find SSLs button the options display below.... just a thought!

Please ask any questions you have.

Thanks.
Marcus

Industry/Entity Type

It Company

Requirements
Must have
• logos of the brands we are selling and we are platinum partners of each.

logo's of brands that use our ssls - please choose some example ones.

Nice to have
• nice to have a most popular either for each one or across the site

```html
<!DOCTYPE html>
<html lang="en">
<head>
<meta charset="utf-8">
<title>74tlq – SSL Certificates</title>
<link href="https://fonts.googleapis.com/css2?family=Figtree:wght@400;600;700&family=Arimo:wght@400;700&display=swap" rel="stylesheet">
<style>
:root{
  --ink:#222;
  --topbar:#3f3f3f;
  --navbar:#d0d0d0;
  --sky:#3dbde0;
  --why:#4cc3e4;
  --domain:#0ea2cf;
  --org:#15c98b;
  --ext:#e99a2b;
  --red:#b3201f;
  --card:#12c57f;
  --card-accent:#ffe93a;
  --partners:#f2f2f2;
  --footer:#444;
  --footer-text:#ddd;
  --head:"Figtree",sans-serif;
  --body:"Arimo",sans-serif;
}
*{margin:0;padding:0;box-sizing:border-box}
html,body{width:1200px;height:3165px;overflow:hidden}
body{font-family:var(--body);color:var(--ink);background:#fff;position:relative}
section,header,footer,nav{position:absolute;left:0;width:1200px}
.abs{position:absolute}

/* top bar */
.topbar{top:0;height:58px;background:var(--topbar);color:#fff}
.brand{font-family:var(--head);font-weight:700;font-size:38px;left:158px;top:6px;color:#fff}
.live-chat{left:554px;top:19px;font-size:17px}
.regions{left:680px;top:22px;font-size:12px;color:#ccc}
.search{left:786px;top:18px;width:242px;height:22px;background:#fff;border-radius:2px}
.search svg{position:absolute;right:8px;top:4px}

/* nav */
.navbar{top:58px;height:63px;background:var(--navbar)}
.navbar a{position:absolute;top:22px;font-size:17px;color:#333;text-decoration:none}

/* hero */
.hero{top:121px;height:586px;text-align:center}
.hero h1{font-family:var(--head);font-weight:600;font-size:78px;line-height:80px;color:var(--sky);position:absolute;top:110px;width:100%;letter-spacing:-1px}
.hero .lead{position:absolute;top:290px;width:100%;font-size:27px;line-height:38px;color:#333}
.url-input{left:256px;top:406px;width:474px;height:64px;background:#e6e6e6;border:2px solid #cfcfcf;border-radius:6px;text-align:left;padding-left:28px;line-height:60px;font-size:21px;color:#888}
.find-btn{left:746px;top:406px;width:198px;height:64px;border-radius:6px;background:linear-gradient(#8ad63d,#5cb11f);color:#fff;font-size:22px;line-height:64px;box-shadow:0 3px 0 #4a8d19}

/* why */
.why{top:707px;height:469px;background:var(--why);color:#fff;text-align:center}
.why h2{position:absolute;top:70px;width:100%;font-family:var(--head);font-weight:700;font-size:84px}
.feature{position:absolute;top:210px;width:320px}
.feature svg{display:block;margin:0 auto 10px}
.feature h3{font-size:26px;font-weight:700;color:#111;margin-bottom:12px}
.feature p{font-size:17px;line-height:24px;color:#134a5a}

/* trial */
.trial{top:1176px;height:530px;background:#fff}
.trial-photo{left:153px;top:16px;width:456px;height:514px;background:linear-gradient(170deg,#c9b9a8,#2f3340 70%)}
.trial-card{left:256px;top:306px;width:258px;height:176px;background:var(--card);color:#fff;padding:28px 20px 0;font-weight:700;white-space:nowrap}
.trial-card .small{display:block;font-size:24px;line-height:30px}
.trial-card .big{display:block;color:var(--card-accent);font-size:36px;line-height:42px}
.trial-card .sub{display:block;font-size:20px;line-height:28px}
.trial-copy{left:620px;top:128px;width:420px}
.trial-copy h2{font-family:var(--head);font-weight:700;font-size:42px;color:var(--red);margin-bottom:16px}
.trial-copy h3{font-size:21px;font-weight:700;margin-bottom:10px}
.trial-copy p{font-size:16px;line-height:24px;margin-bottom:24px}

/* products */
.products{top:1706px;height:456px;background:var(--domain)}
.products h2{position:absolute;top:50px;width:100%;text-align:center;font-family:var(--head);font-weight:700;font-size:72px;color:#fff}
.divider{left:185px;top:172px;width:830px;height:2px;background:rgba(255,255,255,.35)}
.tier{position:absolute;left:0;width:1200px}
.tier-name{position:absolute;right:768px;text-align:right;font-family:var(--head);font-weight:600;font-size:42px;line-height:48px;color:rgba(255,255,255,.82)}
.tier-body{position:absolute;left:488px;width:610px}
.tier-body h3{font-size:22px;font-weight:700;color:#111;margin-bottom:10px}
.tier-body p{font-size:17px;line-height:23px;color:#fff;margin-bottom:14px}
.learn{display:inline-block;width:184px;height:48px;background:#fff;border-radius:5px;text-align:center;line-height:48px;font-size:20px;color:#222}
.notch{position:absolute;left:560px;top:0}
.org{top:2162px;height:283px;background:var(--org)}
.ext{top:2445px;height:298px;background:var(--ext)}

/* partners */
.partners{top:2743px;height:152px;background:var(--partners)}
.partner{position:absolute;top:62px;font-size:28px;font-weight:700;display:flex;align-items:center;gap:10px}
.partner .dot{width:26px;height:26px;border-radius:50%}

/* footer */
.site-footer{top:2895px;height:270px;background:var(--footer);color:var(--footer-text)}
.site-footer .brand{left:185px;top:80px;color:#bbb;font-size:40px}
.foot-links{left:185px;top:140px;font-size:17px}
.foot-links span{margin:0 10px}
.copy{left:185px;top:167px;font-size:15px}
.contact{right:180px;top:72px;text-align:right;font-size:17px;line-height:25px}
.contact.addr{top:148px}
</style>
</head>
<body>

<header class="topbar">
  <div class="abs brand">74tlq</div>
  <div class="abs live-chat">LIVE CHAT</div>
  <div class="abs regions">Regions ▾</div>
  <div class="abs search">
    <svg width="14" height="14" viewBox="0 0 14 14"><circle cx="5.5" cy="5.5" r="4" fill="none" stroke="#333" stroke-width="2"/><line x1="8.5" y1="8.5" x2="13" y2="13" stroke="#333" stroke-width="2"/></svg>
  </div>
</header>

<nav class="navbar">
  <a style="left:432px">Products</a>
  <a style="left:540px">Partners</a>
  <a style="left:641px">Support</a>
  <a style="left:744px">Resources</a>
  <a style="left:862px">Contact us</a>
  <a style="left:978px">Sign In</a>
</nav>

<section class="hero">
  <h1>Protect Your Website<br>&amp; Grow Your Business</h1>
  <p class="lead">Check out our new reduced prices on organization<br>and extended validation SSL!</p>
  <div class="abs url-input">Enter your website here</div>
  <div class="abs find-btn">Find SSLs</div>
</section>

<section class="why">
  <h2>Why choose 74tlq?</h2>
  <div class="feature" style="left:138px">
    <svg width="60" height="70" viewBox="0 0 60 70"><path d="M20 20v-6a10 10 0 0 1 20 0v6" fill="none" stroke="#fff" stroke-width="4"/><rect x="6" y="20" width="48" height="48" rx="4" fill="#fff"/><text x="30" y="56" text-anchor="middle" font-size="30" font-family="Arimo,sans-serif" fill="#4cc3e4">$</text></svg>
    <h3>Fixed Pricing</h3>
    <p>Find out what you will pay up front.<br>No hidden surprises.</p>
  </div>
  <div class="feature" style="left:440px">
    <svg width="60" height="70" viewBox="0 0 60 70"><rect x="24" y="2" width="12" height="7" fill="#fff"/><circle cx="30" cy="40" r="24" fill="none" stroke="#fff" stroke-width="5"/><line x1="30" y1="40" x2="30" y2="24" stroke="#fff" stroke-width="4"/><line x1="30" y1="40" x2="42" y2="46" stroke="#fff" stroke-width="4"/></svg>
    <h3>Money back guarantee</h3>
    <p>We're here when you've got an urgent<br>project you need turned around fast.</p>
  </div>
  <div class="feature" style="left:737px">
    <svg width="60" height="70" viewBox="0 0 60 70"><path d="M14 6h32v18a16 16 0 0 1-32 0z" fill="#fff"/><path d="M14 12H4a10 10 0 0 0 10 14M46 12h10a10 10 0 0 1-10 14" fill="none" stroke="#fff" stroke-width="4"/><rect x="26" y="40" width="8" height="14" fill="#fff"/><rect x="16" y="54" width="28" height="8" fill="#fff"/></svg>
    <h3>We are the best</h3>
    <p>We didn't become #1 by accident.<br>Just ask our customers.</p>
  </div>
</section>

<section class="trial">
  <div class="abs trial-photo" role="img" aria-label="Photo of a smiling businesswoman holding up a trial offer card"></div>
  <div class="abs trial-card">
    <span class="small">Get a</span>
    <span class="big">Free 30-Day</span>
    <span class="sub">SSL Trial Certificate</span>
  </div>
  <div class="abs trial-copy">
    <h2>Try it NOW!</h2>
    <h3>Try before you buy...for free</h3>
    <p>The free* 74tlq SSL Trial offers a fully functioning SSL certificate. Now you can make a true evaluation of your SSL needs before you purchase.</p>
    <p>PlinWard SSL certificates help ensure that your customers' and business partners' information is secure when they use your site. Secure your site in minutes with the PlinWard SSL Trial certificate, enabling up to 256-bit encryption.*</p>
  </div>
</section>

<section class="products">
  <h2>What you get from 74tlq</h2>
  <div class="abs divider"></div>
  <svg class="abs" style="left:560px;top:174px" width="50" height="24" viewBox="0 0 50 24"><path d="M0 0h50L25 24z" fill="#0a86ad"/></svg>
  <div class="tier" style="top:285px">
    <div class="tier-name" style="top:10px">Domain<br>SSL</div>
    <div class="tier-body" style="top:-30px">
      <h3>Fast &amp; Economical</h3>
      <p>Quick issuance SSL Certificate &amp; Secure Site Seal. SSL without any<br>paperwork or fuss &amp; delivered in minutes!</p>
      <span class="learn">Learn More</span>
    </div>
  </div>
</section>

<section class="org">
  <svg class="notch" width="50" height="24" viewBox="0 0 50 24"><path d="M0 0h50L25 24z" fill="#0ea2cf"/></svg>
  <div class="tier" style="top:88px">
    <div class="tier-name">Organization<br>SSL</div>
    <div class="tier-body" style="top:-24px">
      <h3>High Assurance SSL</h3>
      <p>High assurance SSL with full organisation verification displays<br>enhanced levels of trust and security.</p>
      <span class="learn">Learn More</span>
    </div>
  </div>
</section>

<section class="ext">
  <svg class="notch" width="50" height="24" viewBox="0 0 50 24"><path d="M0 0h50L25 24z" fill="#15c98b"/></svg>
  <div class="tier" style="top:90px">
    <div class="tier-name">Extended<br>SSL</div>
    <div class="tier-body" style="top:-22px">
      <h3>Activate the Green Address Bar!</h3>
      <p>The highest assurance level of website trust - visitors see the green<br>bar and enhanced trust means enhanced sales. EV SSL is preferred<br>by all major online brands.</p>
      <span class="learn">Learn More</span>
    </div>
  </div>
</section>

<section class="partners">
  <div class="partner" style="left:186px;color:#8a3b2a">MellowTLS</div>
  <div class="partner" style="left:436px;color:#333"><span class="dot" style="background:#f2b705"></span>Corvalux</div>
  <div class="partner" style="left:624px;color:#333"><span class="dot" style="background:#d52a2a"></span>Brimlo</div>
  <div class="partner" style="left:850px;color:#444"><span class="dot" style="background:#1f6fb8"></span>PlinWard</div>
</section>

<footer class="site-footer">
  <div class="abs brand">74tlq</div>
  <div class="abs foot-links">About<span>|</span>Contact Us<span>|</span>Products<span>|</span>Terms &amp; Conditions</div>
  <div class="abs copy">© 2013 74tlq. All Rights Reserved.</div>
  <div class="abs contact">contact@74tlq.com<br>1.555.010.0199</div>
  <div class="abs contact addr">4417 Harrow Crest Ave. #2209<br>Larkfield, CA 90211</div>
</footer>

</body>
</html>
```